Medical Practice and Business Coaching Website Design

I need a professional website designed for a medical business, TQP Medical.
The website will be hosted on Vorluna (similar design functionality as ZEPT).

About the website:
Pages for the website:
- Home page (a brief overview of the company with a section for "Ultrasound Clinics" and "Coaching and Courses" that link to these pages with all the info and packages for these sections)
- About Us (section for company info and info about Delphine Ashcombe, founder and business coach)
- Ultrasound Clinics (all the info about ultrasound, our packages, links to book, gallery of 3D/4D images, FAQs, social media links)
- Coaching and Courses (All of our coaching package info, course info with a waiting list sign up, section for free business download resources, social media links, blog posts)
- Contact Us (info for our harrowgate ultrasound location and bookings with a map, contact form, email and phone details)

Pages that are also needed but not visible in the top menu:
- Blog Page
- Waiting List Page x2 (Kelbrook pop-up 3D clinic, Online Course)
- Thanks for subscribing page

We have a company logo and a logo for both the ultrasound clinics and the Coaching sides of the business. They are attached as well as the HEX codes for the branding colours. Ideally the company areas of the site will be in the blue, purple and teal colours. The ultrasound clinics page will be mostly in the purple with the "clinics" logo featuring on the page.
The courses and coaching page will be dominant in the blue branding colours with accents of purple and teal. The courses logo will be somewhere on the page too.

About our company:
Our company has 2 separate businesses which will have their own pages on the website.
We have a medical imaging business which specialises in ultrasound. We have 3 locations/services:
- Harrowgate Ultrasound: open Fridays and the occasional saturday. Our main focus and where the focus on the clinical page needs to be.
- East Corrimbal Ultrasound: Currently closed, no re-opening date and unlikely to reopen.
- Pop-up clinics: most commonly occur in Kelbrook. occasionally in Parkes. Dates for next pop-up will be announced in the future.

Our Harrowgate practice offers both diagnostic ultrasound (referral from doctor) for all areas of the body and 3d/4d pregnancy ultrasounds for entertainment purposes.
The content for the ultrasound clinics part of the website can be found on the current harrowgate ultrasound website: harrowgateultrasound.com.au
This website will be replaced by the new company site. All of the info on this site will end up on the clinics page of the new company website.

The second part of the company is a coaching and courses service for medical professionals who want to start or grow their business.
We currently have coaching packages for 1-on-1 online advice and guidance.

Coaching: all take place on Zoom and can be recorded for them to watch again after. Notes, documents and links that are discussed are provided after session

- FREE 15 minute session: discuss current business or business idea, if and how I can help and potential things they can do. One per client

- Single Coaching Session - 1hr with Delphine

- Silver coaching package: 1 x 1hr Coaching Call with Delphine
Unlimited Email with Delphine for 1 month
Access to our Private Facebook Group to network with other medical professionals and business owners

- Silver Coaching Package With Social Media Management:
As above with 1 month Social Media Management (15 posts, Facebook and Instagram)

- Gold coaching package: 2 x 1hr Coaching Calls with Delphine
Access to our Private Facebook

- Gold Coaching Package With Social Media Management:

- Business Sidekick Package: Unlimited Coaching Calls
Unlimited SMS
Unlimited Emails
Social Media Management (Facebook and Instagram, 1 post per day) Valued at over $700
Business Masterclass (something different each month...social media, medicare, website, branding, live events, etc)

Enrollment for our first course opens in May and clients can join the waitlist in the meantime.
Course is aimed at medical professionals who want to grow their patient numbers and create an online presence for their business.
Ideal for: small practices where the owner does everything, not necessarily familiar with marketing/social media/websites, goes to the very basics and steps through everything in getting a logo, branding, website, building social media pages, creating content.

Course name to come but it will be something like "helpful marketing in healthcare" or "the business of healthcare"

We will also have a blog on the website and a podcast (in the future).

I would like a testimonial on at least the clinics page and the coaching page. Here is one for each but I have more if need be:
Coaching: "I knew I wanted to start my own business but I had no idea where to begin. It would have been easy to abort my dreams of starting my own business had it not been for the direction and unwavering support of Delphine from TQP medical. Delphine dissected the process into manageable bit sized pieces for me and worked tirelessly behind the scenes ensuring everything was on track. Her friendly, warm and approachable manner
equated to more than her just being my business coach, she has now become a friend.
Thank you!!"

Ultrasound testimonial: "Amazing service! Best ultrasound experience I’ve had. Super friendly and informative staff. Great technology. If I didn’t live so far away I’d go to Harrowgate for all my ultrasounds!"

I would also like a section for a welcome video (yet to be recorded) on the home page, ultrasound clinics page and coaching/courses page.

I've attached the company logo and the sub-logos in different formats. There is also a head shot of Delphine for the about us page, an image of Delphine with a coaching client for the coaching page and multiple 3D ultrasound images for the gallery on the clinics page.

Target Market(s)

Mostly targeted at medical professionals. Pregnant women and anyone needing an ultrasound are the targets for the clinics page

Industry/Entity Type

Healthcare

Number of Pages Required

5+ page

Colors
0054AA
0677BA
7BADD7
CADEEF
E8F1F8
0094D4
00A9DD
6FCCEA
C7EBF8
E9F6FB
00AB8E
00BBA5
67D7C9
C6EFE9
E9F9F6
A7469A
B969AE
D3A5CF
EDDBEB
F8F0F9
6B429C
8869AF
B7A5CE
E3DAEB
F3F0F8

```html
<!DOCTYPE html>
<html lang="en">
<head>
<meta charset="utf-8">
<title>TQP Medical – Home Page Layouts</title>
<link href="https://fonts.googleapis.com/css2?family=Libre+Bodoni:wght@400;700&family=Poppins:wght@400;500&display=swap" rel="stylesheet">
<style>
:root{
  --navy:#2e3192;
  --blue:#0054aa;
  --sky:#0094d4;
  --teal:#00ab8e;
  --teal-soft:#00bba5;
  --magenta:#a7469a;
  --purple:#6b429c;
  --lilac:#b7a5ce;
  --ink:#111111;
  --grey:#777777;
  --rule:#dddddd;
  --white:#ffffff;
  --board-a:#4fb4b8;
  --board-b:#8a6db6;
  --board-c:#5b5ba8;
}
*{box-sizing:border-box;margin:0;padding:0}
html,body{width:768px;height:1200px;overflow:hidden}
body{
  position:relative;
  font-family:"Libre Bodoni",serif;
  background:linear-gradient(160deg,var(--board-a) 0%,var(--board-b) 30%,var(--board-c) 55%,var(--board-a) 80%,var(--board-c) 100%);
}
.page{position:absolute;width:270px;background:var(--white);overflow:hidden}
.page--photo{left:77px;top:79px;height:997px}
.page--gradient{left:378px;top:79px;height:956px}
.abs{position:absolute}

/* header */
.top-bar{left:0;top:0;width:270px;height:12px;background:linear-gradient(90deg,var(--navy),var(--teal) 45%,var(--purple))}
.social{display:flex;gap:3px}
.social span{width:4px;height:4px;border-radius:50%;background:currentColor;display:block}
.top-bar .social{position:absolute;left:153px;top:4px;color:var(--white)}
.top-bar .call{position:absolute;left:196px;top:3px;font-size:3.8px;color:var(--white);white-space:nowrap}
.nav{font-size:3.8px;color:var(--ink);white-space:nowrap}
.nav a{position:absolute;color:inherit;text-decoration:none}
.brand{position:absolute;text-align:center;font-size:5px;letter-spacing:.4px;color:var(--purple);line-height:1;white-space:nowrap}
.brand-dot{display:block;margin:0 auto 2px;border:1.5px solid var(--teal);border-radius:50%;background:var(--white)}

/* heroes */
.hero-photo{left:0;top:40px;width:270px;height:143px;background:linear-gradient(120deg,#6c6d72,#3d3e44 60%,#55565c);clip-path:ellipse(170% 100% at 50% 0)}
.hero-video{left:135px;top:71px;width:119px;height:79px;background:radial-gradient(circle at 45% 45%,#c9a98a,#6b4f3a 40%,#050505 65%)}
.hero-title{left:37px;top:88px;width:95px;font-size:8px;font-weight:700;color:var(--white);line-height:1.35;text-transform:uppercase}
.play{position:absolute;border-radius:50%;background:linear-gradient(135deg,var(--sky),var(--purple));border:1.5px solid var(--white)}
.play::after{content:"";position:absolute;left:38%;top:28%;border-left:5px solid var(--white);border-top:3px solid transparent;border-bottom:3px solid transparent}
.hero-gradient{left:0;top:0;width:270px;height:144px;background:radial-gradient(circle at 50% 55%,#1cb3ab 0%,#1e8fb0 35%,#3a3fa0 70%,#4b2f95 100%)}
.hero-tab{left:23px;top:0;width:43px;height:57px;background:var(--white);border-radius:0 0 22px 22px}
.hero-heading{left:0;top:65px;width:270px;text-align:center;font-size:7.2px;color:var(--white);line-height:1.35;text-transform:uppercase}

/* text blocks */
.eyebrow{left:0;width:270px;text-align:center;font-size:7.2px;font-weight:700;text-transform:uppercase;background:linear-gradient(90deg,var(--purple),var(--teal));-webkit-background-clip:text;background-clip:text;color:transparent}
.lead{left:50px;width:170px;text-align:center;font-size:5.2px;line-height:1.45;color:var(--ink)}
.body-copy{left:48px;width:174px;text-align:center;font-size:3.5px;line-height:1.45;color:var(--grey)}
.wave{left:0;width:270px;height:85px;background:radial-gradient(ellipse 70% 30% at 55% 55%,rgba(103,215,201,.35),rgba(183,165,206,.25) 55%,transparent 75%)}

/* service rows */
.service-title{font-size:7.2px;font-weight:700;line-height:1.3;text-transform:uppercase}
.service-title--clinic{color:var(--magenta)}
.service-title--course{color:var(--sky)}
.service-copy{width:72px;font-size:3.3px;line-height:1.35;color:var(--grey)}
.btn{position:absolute;width:33px;height:12px;border-radius:6px;color:var(--white);font-size:3.4px;font-weight:700;text-align:center;line-height:12px;letter-spacing:.3px}
.btn--clinic{background:linear-gradient(90deg,var(--magenta),var(--purple))}
.btn--course{background:linear-gradient(90deg,var(--sky),var(--navy))}
.sub-brand{position:absolute;width:40px;text-align:center;font-size:5px;line-height:1.05;letter-spacing:.4px;white-space:nowrap}
.sub-brand .brand-dot{width:24px;height:24px;border-width:2px}
.sub-brand--clinic{color:var(--purple)}.sub-brand--clinic .brand-dot{border-color:var(--magenta)}
.sub-brand--course{color:var(--blue)}.sub-brand--course .brand-dot{border-color:var(--sky)}
.ring{position:absolute;border-radius:50%;background:var(--white)}
.ring--clinic{border:1.5px solid var(--purple);box-shadow:inset 0 0 0 4px var(--white),inset 0 0 0 5.5px var(--magenta)}
.ring--course{border:1.5px solid var(--navy);box-shadow:inset 0 0 0 4px var(--white),inset 0 0 0 5.5px var(--sky)}
.ring .photo{position:absolute;inset:8px;border-radius:50%}
.photo--team{background:linear-gradient(160deg,#e8e2dc,#d7c2b2 45%,#c44d3c 70%,#9a6a55)}
.photo--scan{background:radial-gradient(circle at 45% 45%,#d9b48f,#8a6142 45%,#060606 70%)}
.connector{position:absolute;border:0.6px solid var(--rule)}

/* blog */
.blog-title{left:0;width:270px;text-align:center;font-size:8.2px;font-weight:700;background:linear-gradient(90deg,var(--navy),var(--teal));-webkit-background-clip:text;background-clip:text;color:transparent}
.post{position:absolute;width:66px;text-align:center}
.post-image{width:58px;height:58px;margin:0 auto;border-radius:50%;border:1.5px solid var(--purple);padding:2.5px;background:var(--white)}
.post-image div{width:100%;height:100%;border-radius:50%}
.post--1 .post-image div{background:linear-gradient(150deg,#e3e8ee,#a9b6c4 50%,#caa38d)}
.post--2 .post-image{border-color:var(--teal)}
.post--2 .post-image div{background:linear-gradient(170deg,#2c3f55,#8fb6d6 45%,#dcd2cc)}
.post--3 .post-image{border-color:var(--navy)}
.post--3 .post-image div{background:linear-gradient(160deg,#d8cfc7,#8d7c70 45%,#e2b69a)}
.post h3{margin-top:6px;font-size:3.2px;font-weight:700;line-height:1.4;color:var(--ink)}
.post p{margin-top:2px;font-size:3.1px;line-height:1.4;color:var(--grey)}
.post time{display:block;margin-top:3px;font-family:"Poppins",sans-serif;font-size:3px;color:var(--navy)}
.divider{position:absolute;height:0;border-top:0.6px solid var(--rule)}
.brand-row .sub-brand{width:54px;font-size:4px;letter-spacing:.2px}
.brand-row .sub-brand .brand-dot{width:22px;height:22px}
.tone-teal{color:var(--teal)}.tone-teal .brand-dot{border-color:var(--teal-soft)}

/* footer */
.footer-shape{left:0;width:270px}
.footer-text{font-size:3.4px;color:var(--white);line-height:1.8;white-space:nowrap}
.footer-text h4{font-size:3.9px;font-weight:400}
.footer-text li{list-style:none;font-size:2.9px;color:#aaa;padding-left:4px}
.footer-email{width:50px;border-bottom:0.6px solid var(--white);font-size:3.2px;color:var(--white)}
.btn--signup{width:25px;height:9px;line-height:9px;border-radius:5px;font-size:3px;background:linear-gradient(90deg,var(--sky),var(--navy))}
.copyright{font-size:2.9px;color:var(--white);white-space:nowrap}
.footer-rule{border-top:0.6px solid #444}
</style>
</head>
<body>

<!-- Desktop variant with photographic hero -->
<main class="page page--photo">
  <div class="abs top-bar">
    <div class="social"><span></span><span></span><span></span><span></span><span></span></div>
    <div class="call">&#9742; Call Us: 555 201 6684</div>
  </div>
  <div class="brand" style="left:30px;top:2px;width:34px">
    <span class="brand-dot" style="width:22px;height:22px"></span>TQP MEDICAL
  </div>
  <nav class="nav">
    <a style="left:76px;top:27px">Home</a><a style="left:98px;top:27px">About Us</a><a style="left:125px;top:27px">Ultrasound Clinics</a><a style="left:170px;top:27px">Coaching and Courses</a><a style="left:223px;top:27px">Contact Us</a>
  </nav>

  <div class="abs hero-photo" role="img" aria-label="Photo of a sonographer at an ultrasound machine"></div>
  <div class="abs hero-video" role="img" aria-label="Welcome video still showing a 3D baby scan"></div>
  <div class="play" style="left:186px;top:102px;width:18px;height:18px"></div>
  <h1 class="abs hero-title">TQP Medical is one of the biggest ultrasound clinics practice</h1>

  <h2 class="abs eyebrow" style="top:208px">Welcome to TQP Medical</h2>
  <p class="abs lead" style="top:221px">Lorem ipsum dolor sit amet, consectetur adipiscing elit, sed do eiusmod tempor incididunt ut labore magna aliqua.</p>
  <p class="abs body-copy" style="top:242px">Lorem ipsum dolor sit amet, consectetur adipiscing elit, sed do eiusmod tempor incididunt ut labore et dolore magna aliqua. Quis ipsum suspendisse ultrices gravida. Risus commodo viverra maecenas accumsan lacus vel facilisis. Lorem ipsum dolor sit amet, consectetur adipiscing elit, sed do eiusmod tempor incididunt ut labore et dolore magna aliqua. Quis ipsum suspendisse ultrices gravida. Risus commodo viverra maecenas accumsan lacus vel facilisis.</p>
  <div class="abs wave" style="top:262px" role="img" aria-label="Soft flowing wave decoration"></div>

  <div class="connector" style="left:45px;top:412px;width:93px;height:46px;border-top:0;border-right:0;border-radius:0 0 0 6px"></div>
  <div class="connector" style="left:137px;top:458px;width:1px;height:23px;border-width:0 0 0 .6px"></div>

  <div class="sub-brand sub-brand--clinic" style="left:27px;top:364px"><span class="brand-dot"></span>TQP<br>CLINICS</div>
  <h3 class="abs service-title service-title--clinic" style="left:73px;top:360px">Ultrasound<br>Clinics</h3>
  <p class="abs service-copy" style="left:73px;top:385px">Lorem ipsum dolor sit amet, consectetur adipiscing elit, sed do eiusmod tempor incididunt ut lablorore et dolore magna ali qua uis ipsum suspendisse uloreltrices avida sus commodo viverloyra maecenas accusan lacus vel facilisis. Lorem ipsum dolor sit aet, consectetur adipiscing elit, sed do eiusmod tempor incididunt ut labore et dolore magna aliquacommodo viverra maecenas accsan la cus vel facilisis.</p>
  <div class="btn btn--clinic" style="left:73px;top:432px">READ MORE</div>
  <div class="ring ring--clinic" style="left:156px;top:357px;width:92px;height:92px"><div class="photo photo--team" role="img" aria-label="Photo of two clinic staff members in the scan room"></div></div>

  <div class="ring ring--course" style="left:20px;top:473px;width:92px;height:92px"><div class="photo photo--scan" role="img" aria-label="3D ultrasound image of a baby"></div></div>
  <div class="sub-brand sub-brand--course" style="left:116px;top:481px"><span class="brand-dot"></span>TQP<br>COURSES</div>
  <h3 class="abs service-title service-title--course" style="left:162px;top:477px">Coaching<br>and Courses</h3>
  <p class="abs service-copy" style="left:162px;top:501px">Lorem ipsum dolor sit amet, consectetur adipiscing elit, sed do eiusmod tempor incididunt ut lablorore et dolore magna ali qua uis ipsum suspendisse uloreltrices avida sus commodo viverloyra maecenas accusan lacus vel facilisis. Lorem ipsum dolor sit aet, consectetur adipiscing elit, sed do eiusmod tempor incididunt ut labore et dolore magna aliquacommodo viverra maecenas accsan la cus vel facilisis.</p>
  <div class="btn btn--course" style="left:162px;top:548px">READ MORE</div>
  <div class="abs wave" style="top:562px" role="img" aria-label="Soft flowing wave decoration"></div>

  <h2 class="abs blog-title" style="top:664px">LATEST BLOG POSTS</h2>
  <article class="post post--1" style="left:32px;top:688px"><div class="post-image"><div role="img" aria-label="Photo of a patient during an ultrasound"></div></div><h3>LOREM IPSUM DOLOR SIT AM CONS ECTETUR ASCING</h3><p>Lorem ipsum dolor sit amet, consec tet ur adipiscing elit, sed do eiusmod tem por incididunt ut lablorvel facilisis.</p><time>&#9632; March 18</time></article>
  <article class="post post--2" style="left:102px;top:688px"><div class="post-image"><div role="img" aria-label="Photo of an ultrasound probe on a belly"></div></div><h3>LOREM IPSUM DOLOR SIT AM CONS ECTETUR ASCING</h3><p>Lorem ipsum dolor sit amet, consec tet ur adipiscing elit, sed do eiusmod tem por incididunt ut lablorvel facilisis.</p><time>&#9632; March 18</time></article>
  <article class="post post--3" style="left:174px;top:688px"><div class="post-image"><div role="img" aria-label="Photo of a scan print held over a belly"></div></div><h3>LOREM IPSUM DOLOR SIT AM CONS ECTETUR ASCING</h3><p>Lorem ipsum dolor sit amet, consec tet ur adipiscing elit, sed do eiusmod tem por incididunt ut lablorvel facilisis.</p><time>&#9632; March 18</time></article>
  <div class="divider" style="left:33px;top:805px;width:204px"></div>

  <div class="brand-row">
    <div class="sub-brand sub-brand--clinic" style="left:24px;top:812px"><span class="brand-dot"></span>TQP<br>CLINICS</div>
    <div class="sub-brand sub-brand--course" style="left:60px;top:812px"><span class="brand-dot"></span>TQP<br>COURSES</div>
    <div class="sub-brand sub-brand--course" style="left:100px;top:812px"><span class="brand-dot"></span>TQP<br>EDUCATION</div>
    <div class="sub-brand tone-teal" style="left:140px;top:812px"><span class="brand-dot"></span>TQP<br>MARKETPLACE</div>
    <div class="sub-brand tone-teal" style="left:187px;top:812px"><span class="brand-dot"></span>TQP<br>MEDICAL EQUIPMENT</div>
  </div>

  <svg class="abs footer-shape" style="top:840px" width="270" height="157" viewBox="0 0 270 157" aria-hidden="true">
    <defs><linearGradient id="edgeA" x1="0" x2="1"><stop offset="0" stop-color="#6b429c"/><stop offset=".55" stop-color="#00a9dd"/><stop offset="1" stop-color="#2e3192"/></linearGradient></defs>
    <path d="M0 82 C70 40 150 95 270 5 L270 157 L0 157 Z" fill="#000"/>
    <path d="M0 82 C70 40 150 95 270 5" fill="none" stroke="url(#edgeA)" stroke-width="3"/>
  </svg>
  <div class="brand" style="left:30px;top:922px;width:34px"><span class="brand-dot" style="width:22px;height:22px;border-color:var(--purple)"></span>TQP MEDICAL</div>
  <div class="abs footer-text" style="left:80px;top:926px">Home<br>About Us<br>Ultrasound Clinics<br>Coaching and Courses<br>Contact Us</div>
  <div class="abs footer-text" style="left:132px;top:926px">Waiting List<ul><li>&bull; Kelbrook pop-up 3D clinic</li><li>&bull; Online Course</li></ul>Blog page</div>
  <div class="abs footer-text" style="left:186px;top:926px"><h4>Subscribe Newsletter</h4></div>
  <div class="abs footer-email" style="left:186px;top:944px">Email</div>
  <div class="btn btn--signup" style="left:186px;top:954px">SIGN UP</div>
  <div class="divider footer-rule" style="left:33px;top:970px;width:204px"></div>
  <div class="social abs" style="left:38px;top:982px;color:var(--white)"><span></span><span></span><span></span><span></span><span></span></div>
  <div class="abs copyright" style="left:186px;top:981px">Copyrights &copy; 2022 All Rights Reserved</div>
</main>

<!-- Variant with gradient hero -->
<main class="page page--gradient">
  <div class="abs hero-gradient" role="img" aria-label="Purple and teal gradient hero background"></div>
  <div class="abs hero-tab"></div>
  <div class="brand" style="left:26px;top:6px;width:37px;font-size:5.4px"><span class="brand-dot" style="width:28px;height:28px;border-width:2px"></span>TQP MEDICAL</div>
  <nav class="nav" style="color:var(--white)">
    <a style="left:75px;top:13px;color:var(--purple)">Home</a><a style="left:96px;top:13px">About Us</a><a style="left:124px;top:13px">Ultrasound Clinics</a><a style="left:169px;top:13px">Coaching and Courses</a><a style="left:222px;top:13px">Contact Us</a>
  </nav>
  <h1 class="abs hero-heading">One of the biggest<br>ultrasound clinics practice</h1>
  <div class="play" style="left:126px;top:86px;width:18px;height:18px"></div>

  <h2 class="abs eyebrow" style="top:166px">Welcome to TQP Medical</h2>
  <p class="abs lead" style="top:180px">Lorem ipsum dolor sit amet, consectetur adipiscing elit, sed do eiusmod tempor incididunt ut labore magna aliqua.</p>
  <p class="abs body-copy" style="top:202px">Lorem ipsum dolor sit amet, consectetur adipiscing elit, sed do eiusmod tempor incididunt ut labore et dolore magna aliqua. Quis ipsum suspendisse ultrices gravida. Risus commodo viverra maecenas accumsan lacus vel facilisis. Lorem ipsum dolor sit amet, consectetur adipiscing elit, sed do eiusmod tempor incididunt ut labore et dolore magna aliqua. Quis ipsum suspendisse ultrices gravida. Risus commodo viverra maecenas accumsan lacus vel facilisis.</p>
  <div class="abs wave" style="top:222px" role="img" aria-label="Soft flowing wave decoration"></div>

  <div class="connector" style="left:45px;top:375px;width:93px;height:42px;border-top:0;border-right:0;border-radius:0 0 0 6px"></div>
  <div class="connector" style="left:137px;top:417px;width:1px;height:22px;border-width:0 0 0 .6px"></div>

  <div class="sub-brand sub-brand--clinic" style="left:27px;top:323px"><span class="brand-dot"></span>TQP<br>CLINICS</div>
  <h3 class="abs service-title service-title--clinic" style="left:73px;top:320px">Ultrasound<br>Clinics</h3>
  <p class="abs service-copy" style="left:73px;top:345px">Lorem ipsum dolor sit amet, consectetur adipiscing elit, sed do eiusmod tempor incididunt ut lablorore et dolore magna ali qua uis ipsum suspendisse uloreltrices avida sus commodo viverloyra maecenas accusan lacus vel facilisis. Lorem ipsum dolor sit aet, consectetur adipiscing elit, sed do eiusmod tempor incididunt ut labore et dolore magna aliquacommodo viverra maecenas accsan la cus vel facilisis.</p>
  <div class="btn btn--clinic" style="left:73px;top:391px">READ MORE</div>
  <div class="ring ring--clinic" style="left:156px;top:315px;width:92px;height:92px"><div class="photo photo--team" role="img" aria-label="Photo of two clinic staff members in the scan room"></div></div>

  <div class="ring ring--course" style="left:20px;top:432px;width:92px;height:92px"><div class="photo photo--scan" role="img" aria-label="3D ultrasound image of a baby"></div></div>
  <div class="sub-brand sub-brand--course" style="left:116px;top:440px"><span class="brand-dot"></span>TQP<br>COURSES</div>
  <h3 class="abs service-title service-title--course" style="left:162px;top:437px">Coaching<br>and Courses</h3>
  <p class="abs service-copy" style="left:162px;top:461px">Lorem ipsum dolor sit amet, consectetur adipiscing elit, sed do eiusmod tempor incididunt ut lablorore et dolore magna ali qua uis ipsum suspendisse uloreltrices avida sus commodo viverloyra maecenas accusan lacus vel facilisis. Lorem ipsum dolor sit aet, consectetur adipiscing elit, sed do eiusmod tempor incididunt ut labore et dolore magna aliquacommodo viverra maecenas accsan la cus vel facilisis.</p>
  <div class="btn btn--course" style="left:162px;top:507px">READ MORE</div>
  <div class="abs wave" style="top:522px" role="img" aria-label="Soft flowing wave decoration"></div>

  <h2 class="abs blog-title" style="top:621px">LATEST BLOG POSTS</h2>
  <article class="post post--1" style="left:32px;top:646px"><div class="post-image"><div role="img" aria-label="Photo of a patient during an ultrasound"></div></div><h3>LOREM IPSUM DOLOR SIT AM CONS ECTETUR ASCING</h3><p>Lorem ipsum dolor sit amet, consec tet ur adipiscing elit, sed do eiusmod tem por incididunt ut lablorvel facilisis.</p><time>&#9632; March 18</time></article>
  <article class="post post--2" style="left:102px;top:646px"><div class="post-image"><div role="img" aria-label="Photo of an ultrasound probe on a belly"></div></div><h3>LOREM IPSUM DOLOR SIT AM CONS ECTETUR ASCING</h3><p>Lorem ipsum dolor sit amet, consec tet ur adipiscing elit, sed do eiusmod tem por incididunt ut lablorvel facilisis.</p><time>&#9632; March 18</time></article>
  <article class="post post--3" style="left:174px;top:646px"><div class="post-image"><div role="img" aria-label="Photo of a scan print held over a belly"></div></div><h3>LOREM IPSUM DOLOR SIT AM CONS ECTETUR ASCING</h3><p>Lorem ipsum dolor sit amet, consec tet ur adipiscing elit, sed do eiusmod tem por incididunt ut lablorvel facilisis.</p><time>&#9632; March 18</time></article>
  <div class="divider" style="left:33px;top:762px;width:204px"></div>

  <div class="brand-row">
    <div class="sub-brand sub-brand--clinic" style="left:24px;top:769px"><span class="brand-dot"></span>TQP<br>CLINICS</div>
    <div class="sub-brand sub-brand--course" style="left:60px;top:769px"><span class="brand-dot"></span>TQP<br>COURSES</div>
    <div class="sub-brand sub-brand--course" style="left:100px;top:769px"><span class="brand-dot"></span>TQP<br>EDUCATION</div>
    <div class="sub-brand tone-teal" style="left:140px;top:769px"><span class="brand-dot"></span>TQP<br>MARKETPLACE</div>
    <div class="sub-brand tone-teal" style="left:187px;top:769px"><span class="brand-dot"></span>TQP<br>MEDICAL EQUIPMENT</div>
  </div>

  <svg class="abs footer-shape" style="top:797px" width="270" height="159" viewBox="0 0 270 159" aria-hidden="true">
    <defs><linearGradient id="edgeB" x1="0" x2="1"><stop offset="0" stop-color="#6b429c"/><stop offset=".55" stop-color="#00a9dd"/><stop offset="1" stop-color="#2e3192"/></linearGradient></defs>
    <path d="M0 83 C70 40 150 95 270 5 L270 159 L0 159 Z" fill="#000"/>
    <path d="M0 83 C70 40 150 95 270 5" fill="none" stroke="url(#edgeB)" stroke-width="3"/>
  </svg>
  <div class="brand" style="left:30px;top:884px;width:34px"><span class="brand-dot" style="width:22px;height:22px;border-color:var(--purple)"></span>TQP MEDICAL</div>
  <div class="abs footer-text" style="left:80px;top:882px">Home<br>About Us<br>Ultrasound Clinics<br>Coaching and Courses<br>Contact Us</div>
  <div class="abs footer-text" style="left:132px;top:882px">Waiting List<ul><li>&bull; Kelbrook pop-up 3D clinic</li><li>&bull; Online Course</li></ul>Blog page</div>
  <div class="abs footer-text" style="left:186px;top:882px"><h4>Subscribe Newsletter</h4></div>
  <div class="abs footer-email" style="left:186px;top:900px">Email</div>
  <div class="btn btn--signup" style="left:186px;top:910px">SIGN UP</div>
  <div class="divider footer-rule" style="left:33px;top:929px;width:204px"></div>
  <div class="social abs" style="left:38px;top:941px;color:var(--white)"><span></span><span></span><span></span><span></span><span></span></div>
  <div class="abs copyright" style="left:186px;top:939px">Copyrights &copy; 2022 All Rights Reserved</div>
</main>

</body>
</html>
```